Business Card Design Project

I need a business card designed from scratch. I have an existing logo that I can upload in Illustrator for modification or redesign.

The Company is called Query Lanterns http://querylanterns.com.au and we provide Search Engine Optimization services to Australian businesses. The current logo signifies an increase in visitors, profits etc...

There are no restrictions as to the redesign - colours, style etc are all open to change.

Cards will be full colour and one sided printed at http://www.cardmoxel.com.au so check their requirements for file format and sizes etc.

I will expect all original files upon completion of project.

Target Market(s)

Any business with a web site looking to improve their search engine rankings

Industry/Entity Type

Business

Requirements
Must have
• I like modern, sleek designs. Clean, not fussy, uncluttered.

```html
<!DOCTYPE html>
<html lang="en">
<head>
<meta charset="utf-8">
<title>Query Lanterns – Business Card</title>
<link rel="stylesheet" href="https://fonts.googleapis.com/css2?family=Source+Sans+3:wght@400;600;700&display=swap">
<style>
  :root {
    --backdrop: #3b2a20;
    --card: #ffffff;
    --brand-blue: #1a6fb8;
    --band-deep: #1b3a72;
    --band-light: #2d62a8;
    --accent-yellow: #f2be1a;
    --ink: #333333;
    --ink-soft: #444444;
  }
  * { box-sizing: border-box; margin: 0; padding: 0; }
  html, body {
    width: 1200px; height: 412px; overflow: hidden;
    background: var(--backdrop);
    font-family: "Source Sans 3", "Segoe UI", Arial, sans-serif;
  }
  .stage { position: relative; width: 1200px; height: 412px; }
  .card {
    position: absolute; top: 65px;
    width: 497px; height: 284px;
    background: var(--card);
    overflow: hidden;
  }
  .card--front { left: 73px; }
  .card--back { left: 631px; }
  .swoosh { position: absolute; left: 0; top: 0; width: 100%; height: 100%; }
  .brand {
    position: absolute; left: 0; right: 0;
    display: flex; align-items: center; justify-content: center; gap: 10px;
  }
  .brand__dot {
    border-radius: 50%;
    background: var(--accent-yellow);
  }
  .brand__name {
    color: var(--brand-blue);
    font-weight: 700;
    letter-spacing: -0.5px;
    line-height: 1;
  }
  .card--front .brand { top: 54px; }
  .card--front .brand__dot { width: 14px; height: 14px; }
  .card--front .brand__name { font-size: 34px; }
  .card--back .brand { top: 96px; }
  .card--back .brand__dot { width: 18px; height: 18px; }
  .card--back .brand__name { font-size: 46px; }
  .holder {
    position: absolute; top: 139px; left: 0; right: 0;
    text-align: center; color: var(--ink);
  }
  .holder__name { font-size: 16px; font-weight: 700; }
  .holder__title { font-size: 12.5px; font-weight: 400; }
  .contact {
    position: absolute; left: 0; right: 0;
    text-align: center; color: var(--ink-soft);
    font-size: 12px;
  }
  .contact--lines { top: 183px; word-spacing: 1px; }
  .contact--address { top: 206px; }
  .contact__item + .contact__item { margin-left: 8px; }
  .web {
    position: absolute; left: 0; right: 0; top: 238px;
    text-align: center; color: var(--ink);
    font-size: 12.5px; font-weight: 700;
  }
</style>
</head>
<body>
<main class="stage">

  <section class="card card--front" aria-label="Business card front">
    <svg class="swoosh" viewBox="0 0 497 284" preserveAspectRatio="none" aria-hidden="true">
      <defs>
        <linearGradient id="bandFront" x1="0" y1="0" x2="0" y2="1">
          <stop offset="0" stop-color="var(--band-light)"/>
          <stop offset="1" stop-color="var(--band-deep)"/>
        </linearGradient>
      </defs>
      <path d="M0,206 C70,250 160,276 260,284 L0,284 Z" fill="url(#bandFront)"/>
      <path d="M210,284 C320,268 420,248 497,224 L497,284 Z" fill="url(#bandFront)"/>
      <path d="M150,266 C280,262 400,242 497,208" fill="none" stroke="var(--accent-yellow)" stroke-width="3"/>
    </svg>
    <div class="brand">
      <span class="brand__dot"></span>
      <span class="brand__name">Query Lanterns</span>
    </div>
    <p class="holder"><span class="holder__name">Your Name /</span> <span class="holder__title">Title</span></p>
    <p class="contact contact--lines">
      <span class="contact__item">P: 091 234 5678</span>
      <span class="contact__item">C: 091 234 5678</span>
      <span class="contact__item">E: enquiry@querylanterns.com.au</span>
    </p>
    <p class="contact contact--address">Complex name,Street name, City, State, zip code</p>
    <p class="web">www.querylanterns.com.au</p>
  </section>

  <section class="card card--back" aria-label="Business card back">
    <svg class="swoosh" viewBox="0 0 497 284" preserveAspectRatio="none" aria-hidden="true">
      <defs>
        <linearGradient id="bandBack" x1="0" y1="0" x2="0" y2="1">
          <stop offset="0" stop-color="var(--band-light)"/>
          <stop offset="1" stop-color="var(--band-deep)"/>
        </linearGradient>
      </defs>
      <path d="M0,206 C70,250 160,276 260,284 L0,284 Z" fill="url(#bandBack)"/>
      <path d="M210,284 C320,268 420,248 497,224 L497,284 Z" fill="url(#bandBack)"/>
      <path d="M150,266 C280,262 400,242 497,208" fill="none" stroke="var(--accent-yellow)" stroke-width="3"/>
    </svg>
    <div class="brand">
      <span class="brand__dot"></span>
      <span class="brand__name">Query Lanterns</span>
    </div>
    <p class="web">www.querylanterns.com.au</p>
  </section>

</main>
</body>
</html>
```